High-end construction company needs a business card design

We need a modern looking business card that draws people in, is memorable and looks so good people will want to sick it on their fridges.
On the first side what is needed are:
Logo
My name - Tomasz Brelwik
Title - Managing Director
Website - www.varkelt.co.uk
Email - tomasz@varkelt.co.uk
Telephone - 020 5194 6281
Mobile - 07845139072
On the back side was is needed is a list of all the services we provide:
-Kitchen Renovations
-Bathroom Renovations
-House Renovations
-Garage Conversions
-Extensions
-Loft Conversions
-Conservatories
-Carpentry
-Tiling
-Electrical
-Plumbing & Heating
-Bricklaying
-Landscaping
-Decorating
-Plastering
We would like the colours to be the same shades as on the logo with grey or black for the words.
Target Market(s)
Anyone who needs building work done
Contact Information for Business Card
This business card is for a construction company which strives to deliver excellent service and quality.
The look and feel of the card should represent this.
Requirements
Must have
- On the first side what is needed are:
Logo
My name - Tomasz Brelwik
Title - Managing Director
Website - www.varkelt.co.uk
Email - tomasz@varkelt.co.uk
Telephone - 020 5194 6281
Mobile - 07845139072
Nice to have
- Cool looking features

```html
<!DOCTYPE html>
<html lang="en">
<head>
<meta charset="utf-8">
<title>Varkelt Construction Ltd – Business Card</title>
<link href="https://fonts.googleapis.com/css2?family=Poppins:wght@400;500;600;700&display=swap" rel="stylesheet">
<style>
  :root {
    --green: #52b135;
    --green-dark: #3a8f2a;
    --green-light: #7ccf4e;
    --green-deep: #2f7d25;
    --ink: #222222;
    --paper: #ffffff;
    --backdrop: #d9dcdf;
  }
  * { box-sizing: border-box; margin: 0; padding: 0; }
  html, body { width: 1200px; height: 800px; overflow: hidden; }
  body {
    background: var(--backdrop);
    font-family: "Poppins", sans-serif;
    display: flex;
    flex-direction: column;
    align-items: center;
    justify-content: center;
    gap: 36px;
  }
  .card {
    position: relative;
    width: 620px;
    height: 354px;
    overflow: hidden;
    box-shadow: 0 8px 24px rgba(0,0,0,0.18);
  }

  /* Front */
  .card--front { background: var(--paper); }
  .brand {
    position: absolute;
    left: 52px;
    top: 96px;
    display: flex;
    align-items: center;
    gap: 12px;
  }
  .brand__mark {
    width: 18px; height: 18px;
    background: var(--green);
  }
  .brand__name {
    font-weight: 700;
    font-size: 40px;
    letter-spacing: 1px;
    line-height: 1;
    color: var(--green);
  }
  .brand__sub {
    font-weight: 700;
    font-size: 11.5px;
    letter-spacing: 2.6px;
    color: var(--green);
    margin-top: 4px;
  }
  .person {
    position: absolute;
    right: 48px;
    top: 64px;
    text-align: right;
    width: 260px;
    border-bottom: 1.5px solid var(--green);
    padding-bottom: 8px;
  }
  .person__name {
    font-weight: 600;
    font-size: 19px;
    color: var(--green);
    text-transform: uppercase;
    letter-spacing: 0.3px;
  }
  .person__title {
    font-weight: 500;
    font-size: 13px;
    color: var(--ink);
  }
  .website {
    position: absolute;
    right: 48px;
    top: 168px;
    font-weight: 600;
    font-size: 14px;
    color: var(--green);
    letter-spacing: 0.4px;
  }
  .contacts {
    position: absolute;
    left: 52px;
    top: 224px;
    width: 300px;
    border-top: 1.5px solid var(--green);
    padding-top: 8px;
    list-style: none;
  }
  .contacts li {
    display: flex;
    align-items: center;
    gap: 12px;
    font-size: 16px;
    font-weight: 500;
    color: var(--ink);
    line-height: 1.5;
  }
  .contacts svg { width: 15px; height: 15px; fill: var(--green); flex: none; }
  .front-band {
    position: absolute;
    left: 0; right: 0; bottom: 0;
    height: 10px;
    background: var(--green);
    border-top: 3px solid var(--green-light);
  }

  /* Back */
  .card--back {
    background: linear-gradient(120deg, var(--green-light) 0%, var(--green) 45%, var(--green-dark) 100%);
  }
  .back-art {
    position: absolute;
    right: 30px;
    top: 0;
    width: 330px;
    height: 230px;
    background: linear-gradient(160deg, rgba(47,125,37,0.45), rgba(47,125,37,0.15));
    border-radius: 0 0 6px 6px;
  }
  .back-brand {
    position: absolute;
    left: 48px;
    top: 64px;
  }
  .back-brand .brand__name { color: var(--green-light); font-size: 34px; }
  .back-brand .brand__sub { color: var(--green-light); font-size: 9.5px; letter-spacing: 2.3px; }
  .services {
    position: absolute;
    right: 40px;
    bottom: 44px;
    text-align: right;
    color: var(--paper);
    font-weight: 500;
    font-size: 14px;
    line-height: 1.6;
    letter-spacing: 0.2px;
  }
</style>
</head>
<body>

  <section class="card card--front" aria-label="Business card front">
    <div class="brand">
      <span class="brand__mark"></span>
      <div>
        <div class="brand__name">VARKELT</div>
        <div class="brand__sub">CONSTRUCTION LTD</div>
      </div>
    </div>

    <div class="person">
      <div class="person__name">Tomasz Brelwik</div>
      <div class="person__title">Managing Director</div>
    </div>
    <div class="website">www.varkelt.co.uk</div>

    <ul class="contacts">
      <li>
        <svg viewBox="0 0 24 24" aria-hidden="true"><path d="M6.6 10.8a15.1 15.1 0 0 0 6.6 6.6l2.2-2.2a1 1 0 0 1 1-.25 11.4 11.4 0 0 0 3.6.57 1 1 0 0 1 1 1V20a1 1 0 0 1-1 1A17 17 0 0 1 3 4a1 1 0 0 1 1-1h3.5a1 1 0 0 1 1 1c0 1.25.2 2.45.57 3.57a1 1 0 0 1-.25 1z"/></svg>
        07845139072
      </li>
      <li>
        <svg viewBox="0 0 24 24" aria-hidden="true"><path d="M3 9c0-2 4-4 9-4s9 2 9 4v2h-5V9H8v2H3zM6 12h12l2 8H4zm6 2a2.5 2.5 0 1 0 0 5 2.5 2.5 0 0 0 0-5z"/></svg>
        020 5194 6281
      </li>
      <li>
        <svg viewBox="0 0 24 24" aria-hidden="true"><path d="M2 5h20v14H2zm2 2v.5l8 5.5 8-5.5V7zm0 3v7h16v-7l-8 5.5z"/></svg>
        tomasz@varkelt.co.uk
      </li>
    </ul>
    <div class="front-band"></div>
  </section>

  <section class="card card--back" aria-label="Business card back">
    <div class="back-art" role="img" aria-label="Faint excavator arm and house outline decoration"></div>
    <div class="brand back-brand">
      <div>
        <div class="brand__name">VARKELT</div>
        <div class="brand__sub">CONSTRUCTION LTD</div>
      </div>
    </div>
    <div class="services">
      <p>Kitchen Renovations - Bathroom Renovations - House Renovations</p>
      <p>Garage Conversions - Extensions - Loft Conversions - Conservatories</p>
      <p>Carpentry - Tiling - Electrical - Plumbing &amp; Heating - Bricklaying</p>
      <p>Landscaping - Decorating - Plastering</p>
    </div>
  </section>

</body>
</html>
```